$5 Quest Website Required

I am looking for someone to develop a website akin to the simplicity of www.boxlantern.example with a video in the center or a tab that permits one to "Accept the Challenge."

Incorporates our logo and is used to promote our "$5 Quest Program."

Please see attachments, but we are igniting entrepreneurial spirit among our nation's youth through this interactive and intensive program!

There should be a way to navigate to other sections of the site including:

About
Why
Request $5 Quest Packet
Success Stories
Partners
Link to Norvik Holdings
Updates

Thanks to all in advance!

Looking forward to working with you!

Good feel of what we are looking for in terms of "feel"

http://www.thebrightripple.example/

Thank you,

RB

Please make note of this website, we are going for a feel that is akin to this and less modern and professional...more abstract and interactive...but of course include space for our video:

Colors, feel, imagery, is great. Keep your formats, but bring on the feel!

Thank you all for your hard work and patience.

Thank you all for your hard work thus far.

Meanwhile, please understand that the $5 Quest is young, youthful, full of challenge and vitality, it is a competition among students from high school and universities.  The websites you have delivered are too corporate, stale, and standard.  I'm looking for something that is fresh, different, like www.thebrightripple.example.

Symbols, cartoonish, but serious, down to business and save the world one $5 bill at a time.  The logo can be used as a theme...the colors, the feel.

Video space for explanation on the $5 Quest front and center.  With leaves, $ signs, colorful colors, etc.

Visual needs to be compelling to Join the Challenge! Although Norvik Holdings and the tree is a parent company; $5 Quest is separate and Norvik Holdings should only be mentioned as a link.

PixelHarbor.example in regard to simplicity; and www.thebrightripple.example in terms of style.

Thank you,

Raphael

Like the designs that have been submitted; we are almost there.

Target Market(s)

Professors, students, teachers, parents and NGO leaders who wish to use our program as a way to inspire leadership/entrepreneurship/fundraise for their causes.

Requirements
Must have
• Place for the video, front and center
Include logo
Forsight for blogging, message, etc.
Nice to have
• Plan "buckets" to include"
Explanation Video
Two pamphlets
Contract
FAQs
Website with Blog, voting, registration, video upload, etc.
Flyer perfected
Parable...symbol of our life
Photos
Stats included
Testimonials
Organizations that have used (TKWLM, North Brook Lodge, Marlowton High)
Sponsors (Open Lantern, Copperleaf Learningfield)
Photos from events

I understand this takes coding and such, but want you to be aware of the long term vision for it!

```html
<!DOCTYPE html>
<html lang="en">
<head>
<meta charset="utf-8">
<title>$5 Quest</title>
<link href="https://fonts.googleapis.com/css2?family=Roboto+Condensed:wght@400;500;700&family=Arimo:wght@400;700&display=swap" rel="stylesheet">
<style>
  :root{
    --green:#159146;
    --green-dark:#0f7a39;
    --orange:#f39a12;
    --grey-text:#555555;
    --nav-grey:#555555;
    --gold-line:#f1c84a;
    --paper:#fbf3df;
    --paper-deep:#efe0bd;
    --frame:#dcdcdc;
    --ink:#222222;
  }
  *{box-sizing:border-box;margin:0;padding:0}
  html,body{width:1200px;height:1018px;overflow:hidden}
  body{font-family:"Arimo",Arial,sans-serif;color:var(--grey-text);background:var(--paper)}
  .page{position:relative;width:1200px;height:1018px;overflow:hidden}
  .backdrop{position:absolute;inset:0;
    background:radial-gradient(ellipse at 58% 12%,#fffdf6 0%,rgba(255,253,246,0) 45%),
               radial-gradient(ellipse at 70% 78%,#e9dcc0 0%,rgba(233,220,192,0) 55%),
               linear-gradient(180deg,#fcf6e6 0%,var(--paper) 55%,var(--paper-deep) 100%);}
  .abs{position:absolute}

  .utility{top:0;right:34px;display:flex;align-items:center;height:28px;font-family:"Roboto Condensed",sans-serif;font-weight:500;font-size:16px;color:var(--ink)}
  .utility a{color:var(--ink);text-decoration:none;padding:0 10px;letter-spacing:.5px}
  .utility .lang{background:var(--green);color:#fff;font-size:13px;font-weight:700;height:28px;display:flex;align-items:center;gap:12px;padding:0 10px;margin-left:6px;border-radius:0 0 2px 2px}

  .brand{top:40px;left:0;width:1200px;display:flex;justify-content:center;align-items:center;gap:22px}
  .brand-dot{width:120px;height:120px;border-radius:50%;background:var(--green)}
  .brand-name{font-family:"Arimo",sans-serif;font-weight:700;font-size:84px;color:#4a4a4c;letter-spacing:1px}

  .main-nav{top:232px;left:0;width:1200px;display:flex;justify-content:center;align-items:center;font-family:"Roboto Condensed",sans-serif;font-weight:500;font-size:21px;letter-spacing:.6px}
  .main-nav a{color:var(--nav-grey);text-decoration:none}
  .main-nav a.current{color:var(--green)}
  .main-nav .sep{width:6px;height:6px;border-radius:50%;background:var(--green);margin:0 22px}
  .nav-rule{top:276px;left:24px;width:1152px;height:1px;background:var(--gold-line)}

  .welcome{top:330px;left:24px;width:314px}
  .section-title{font-family:"Roboto Condensed",sans-serif;font-weight:400;font-size:21px;color:var(--orange);padding-bottom:10px;border-bottom:2px dotted #8a8a8a}
  .section-title .g{color:var(--green)}
  .welcome p{font-size:14.5px;line-height:21px;text-align:justify;margin-top:12px;color:#5a5a5a}
  .welcome p:first-of-type{margin-top:18px}

  .video-frame{top:300px;left:396px;width:530px;height:442px;border:1px solid var(--gold-line);border-radius:6px;padding:6px;background:rgba(255,255,255,.4)}
  .video-inner{width:100%;height:100%;background:#fff;border:6px solid var(--frame);border-radius:4px;box-shadow:0 10px 14px -8px rgba(0,0,0,.35);position:relative}
  .play{position:absolute;left:168px;top:86px}
  .watch{position:absolute;left:0;width:100%;top:300px;text-align:center;font-family:"Roboto Condensed",sans-serif;font-weight:700;font-size:31px;color:#1d1d1d;letter-spacing:.5px}

  .testimonials{top:330px;left:974px;width:202px}
  .testimonials .section-title{text-align:right;color:var(--green)}
  .testimonials .section-title .o{color:var(--orange)}
  .quote{margin-top:20px}
  .quote p{font-size:14.5px;line-height:19px;text-align:justify;width:170px;color:#5a5a5a}
  .quote .who{text-align:right;font-size:14px;margin-top:12px}
  .quote.first p{margin-left:10px}
  .quote.second{margin-top:36px}

  .cta-line{top:821px;height:0;border-top:2px dashed var(--green)}
  .cta{top:788px;left:444px;width:396px;height:65px}
  .cta-label{position:absolute;inset:0;display:flex;align-items:center;justify-content:center;font-family:"Roboto Condensed",sans-serif;font-size:25px;color:#fff;letter-spacing:.4px}

  .footer-rule{top:902px;left:24px;width:1152px;border-top:2px dotted #bdbdbd}
  .footer-brand{top:928px;left:40px;display:flex;align-items:center;gap:6px;font-family:"Arimo",sans-serif;font-weight:700;font-size:24px;color:var(--green)}
  .footer-brand .dot{width:30px;height:30px;border-radius:50%;background:var(--green)}
  .footer-nav{top:926px;right:40px;display:flex;gap:19px;font-size:13px}
  .footer-nav a{color:var(--ink);text-decoration:none}
  .copyright{top:953px;right:40px;font-size:12.5px;color:#333}
</style>
</head>
<body>
<div class="page">
  <div class="backdrop" role="img" aria-label="Faded background illustration of banknotes and a rising arrow over sun rays"></div>

  <nav class="utility abs">
    <a href="#">FAQ</a>
    <a href="#">SIGNIN</a>
    <span class="lang">LANGUAGE
      <svg width="12" height="9" viewBox="0 0 12 9"><path d="M0 0h12L6 9z" fill="#fff"/></svg>
    </span>
  </nav>

  <header class="brand abs">
    <span class="brand-dot"></span>
    <span class="brand-name">$5 Quest</span>
  </header>

  <nav class="main-nav abs">
    <a href="#" class="current">HOME</a><span class="sep"></span>
    <a href="#">ABOUT US</a><span class="sep"></span>
    <a href="#">WHY WE ARE?</a><span class="sep"></span>
    <a href="#">SUCCESS STORIES</a><span class="sep"></span>
    <a href="#">PARTNERS</a><span class="sep"></span>
    <a href="#">NORVIK HOLDINGS</a>
  </nav>
  <div class="nav-rule abs"></div>

  <section class="welcome abs">
    <h2 class="section-title">WELCOME TO <span class="g">$5 QUEST</span></h2>
    <p>Lorem ipsum dolor sit amet, consectetur adipiscing elit. Curabitur eu nisl odio. Cras egestas turpis in mi feugiat vel tincidunt arcu accumsan. Phasellus non posuere eros. Aenean consectetur.</p>
    <p>sapien in elit luctus ac posuere purus placerat. Aliquam turpis lorem,.</p>
    <p>Donec fermentum sodales erat, quis consequat nisi ornare eget. Duis volutpat justo ut ante imperdiet feugiat. fermentum sodales erat, quis consequat nisi ornare eget. Duis volutpat justo ut ante imperdiet feugiat.</p>
    <p>sapien in elit luctus ac posuere purus placerat. Aliquam turpis lorem,.</p>
  </section>

  <section class="video-frame abs">
    <div class="video-inner">
      <svg class="play" width="176" height="176" viewBox="0 0 176 176" aria-label="Play video">
        <defs>
          <linearGradient id="playFill" x1="0" y1="0" x2="0" y2="1">
            <stop offset="0" stop-color="#3a3a3a"/>
            <stop offset="1" stop-color="#0e0e0e"/>
          </linearGradient>
        </defs>
        <circle cx="88" cy="88" r="87" fill="url(#playFill)"/>
        <path d="M71 54 L121 88 L71 122 Z" fill="#d9d9d9"/>
      </svg>
      <div class="watch">WATCH VIDEO</div>
    </div>
  </section>

  <aside class="testimonials abs">
    <h2 class="section-title">Client <span class="o">Testimonials</span></h2>
    <div class="quote first">
      <p>Lorem ipsum dolor sit amsectetur adipiscing elit. Curabitur eu nisl odio. dolor sit amsectetur u nisl odio.</p>
      <div class="who">- LOREM IPSUM</div>
    </div>
    <div class="quote second">
      <p>Lorem ipsum dolor sit amsectetur adipiscing elit. Curabitur eu nisl odio. dolor sit amsectetur u nisl odio.</p>
      <div class="who">- LOREM IPSUM</div>
    </div>
  </aside>

  <div class="cta-line abs" style="left:302px;width:150px"></div>
  <div class="cta-line abs" style="left:832px;width:152px"></div>
  <a class="cta abs" href="#">
    <svg width="396" height="65" viewBox="0 0 396 65">
      <path d="M0 0H396L382 32.5L396 65H0L14 32.5Z" fill="var(--green)"/>
    </svg>
    <span class="cta-label">ACCEPT THE CHALLENGE</span>
  </a>

  <div class="footer-rule abs"></div>
  <div class="footer-brand abs"><span class="dot"></span>$5 Quest</div>
  <nav class="footer-nav abs">
    <a href="#">Home</a>
    <a href="#">About Us</a>
    <a href="#">Success Stories</a>
    <a href="#">Partners</a>
    <a href="#">Norvik Holdings</a>
    <a href="#">Terms</a>
    <a href="#">Privacy Policy</a>
  </nav>
  <div class="copyright abs">All Rights reserved @ $5quest</div>
</div>
</body>
</html>
```